Borealis Business Card Design

We need a business card design for a new company in NJ called Borealis LLC. We provide plumbing, sewer & drain cleaning, and full bath remodeling services. We need a logo design that will be used for several applications such as; cards, stickers, t shirts, and truck lettering. The company hopes to one day be a full service operation offering plumbing, heating, cooling, electric, so we need a design that is very general (aka no pipe wrenches). Colors will be royal blue,neon lime green, and would like to add diamond plate or steel plate to give it a very masculine feel and look.

Industry/Entity Type

Contact Information for Business Card

Borealis LLC. ,Plumbing, Sewer & Drain Cleaning, Bath Remodeling
North Brunswick, NJ 08902
732.555.0147
Borealispipeworks.example
Info@borealispipeworks.example
Stay calm, ring borealis!, Raul Pemberton- President
NJ Master Plumbing License: 58627, Residential & Commercial Service

Requirements
Should not have
• Tool icons
Script font

```html
<!DOCTYPE html>
<html lang="en">
<head>
<meta charset="utf-8">
<title>Borealis LLC Business Card</title>
<link rel="stylesheet" href="https://fonts.googleapis.com/css2?family=Comfortaa:wght@400&family=Exo+2:wght@400;500&display=swap">
<style>
  :root {
    --backdrop: #3a3430;
    --card: #fbfbfb;
    --brand-blue: #00aeef;
    --ink-dark: #3a3a3a;
    --ink-light: #ffffff;
  }
  * { box-sizing: border-box; margin: 0; padding: 0; }
  html, body {
    width: 1200px; height: 1054px; overflow: hidden;
    background: var(--backdrop);
  }
  .canvas {
    width: 1200px; height: 1054px;
    display: flex; flex-direction: column; align-items: center; justify-content: center;
    gap: 70px;
  }
  .card {
    position: relative;
    width: 700px; height: 400px;
    background: var(--card);
    box-shadow: 0 12px 30px rgba(0,0,0,.45);
    overflow: hidden;
  }
  .brand-name {
    font-family: "Comfortaa", sans-serif;
    font-weight: 400;
    color: var(--brand-blue);
    white-space: nowrap;
    line-height: 1;
  }
  .card-front .brand-name {
    position: absolute; left: 50%; top: 52%;
    transform: translate(-50%, -50%);
    font-size: 72px;
  }
  .card-back .brand-name {
    position: absolute; left: 44px; top: 126px;
    font-size: 68px;
  }
  .person {
    position: absolute; right: 34px; top: 100px;
    text-align: right;
    font-family: "Exo 2", sans-serif;
    letter-spacing: 1px;
  }
  .person-name { color: var(--brand-blue); font-size: 19px; font-weight: 500; }
  .person-title { color: var(--ink-dark); font-size: 14px; font-weight: 500; margin-top: 2px; }
  .info-band {
    position: absolute; left: 0; right: 0; top: 222px; height: 148px;
    background: var(--brand-blue);
    font-family: "Exo 2", sans-serif;
    color: var(--ink-light);
  }
  .contact-list {
    list-style: none;
    position: absolute; left: 30px; top: 18px;
    font-size: 13px; letter-spacing: .5px;
  }
  .contact-list li { display: flex; align-items: center; gap: 10px; height: 22px; white-space: nowrap; }
  .contact-list svg { width: 13px; height: 13px; fill: var(--ink-light); flex: none; }
  .address {
    position: absolute; right: 34px; top: 18px;
    font-size: 14px; letter-spacing: 1px; line-height: 22px; text-align: right;
    white-space: nowrap;
  }
</style>
</head>
<body>
<main class="canvas">
  <section class="card card-front" aria-label="Card front">
    <h1 class="brand-name">Borealis LLC</h1>
  </section>

  <section class="card card-back" aria-label="Card back">
    <h2 class="brand-name">Borealis LLC</h2>
    <div class="person">
      <p class="person-name">RAUL PEMBERTON</p>
      <p class="person-title">PRESIDENT</p>
    </div>
    <div class="info-band">
      <ul class="contact-list">
        <li>
          <svg viewBox="0 0 16 16"><path d="M3.5 1l3 3-1.6 1.8a9 9 0 0 0 5.3 5.3L12 9.5l3 3-2 2.2C7.5 14.5 1.5 8.5 1.3 3z"/></svg>
          <span>732.555.0147</span>
        </li>
        <li>
          <svg viewBox="0 0 16 16"><path d="M2 2h12v12H2zm2 2v8h8V4zm1 1h6v1H5zm0 2h6v1H5zm0 2h4v1H5z"/></svg>
          <span>NJ Master Plumbing License: 58627</span>
        </li>
        <li>
          <svg viewBox="0 0 16 16"><path d="M8 1l6 5v9h-4v-5H6v5H2V6z"/></svg>
          <span>Plumbing, Sewer &amp; Drain Cleaning, Bath Remodeling</span>
        </li>
        <li>
          <svg viewBox="0 0 16 16"><path d="M1 3h14v10H1zm1.5 1.2L8 8.5l5.5-4.3z"/></svg>
          <span>Info@borealispipeworks.example</span>
        </li>
        <li>
          <svg viewBox="0 0 16 16"><path d="M8 1a7 7 0 1 0 0 14A7 7 0 0 0 8 1zm0 1.5c.8 0 1.8 1.6 2.1 4.2H5.9C6.2 4.1 7.2 2.5 8 2.5zM2.6 7.5h2.3a13 13 0 0 0 .3 2.5H3a5.5 5.5 0 0 1-.4-2.5zm8.5 0h2.3a5.5 5.5 0 0 1-.4 2.5h-2.2a13 13 0 0 0 .3-2.5zM6 11h4c-.4 1.6-1.2 2.5-2 2.5S6.4 12.6 6 11z"/></svg>
          <span>Borealispipeworks.example</span>
        </li>
      </ul>
      <p class="address">North Brunswick,<br>NJ 08902</p>
    </div>
  </section>
</main>
</body>
</html>
```